BRIGHTHOLD PROPERTY MANAGEMENT INC. WEBSITE

Please make the website more family-friendly.

I want a website to help me build my property management business by adding listing properties and creating an online application. Im open to any other ideas.
I want a WordPress designer to code it.

Here is my current website. www.brighthold.biz

IDEA: I like the website design https://www.pelicanclimateservices.com/

Thank you

Tom

Number of Pages Required

5+ page

```html
<!DOCTYPE html>
<html lang="en">
<head>
<meta charset="utf-8">
<title>Brighthold Property Management</title>
<link href="https://fonts.googleapis.com/css2?family=Cinzel:wght@600;700&family=Poppins:wght@400;500;600;700&display=swap" rel="stylesheet">
<style>
:root{
  --red:#a6141b;
  --red-dark:#7d0d12;
  --rate:#e2262d;
  --black:#0c0c0c;
  --ink:#1a1a1a;
  --grey:#555;
  --light:#f4f4f4;
  --white:#fff;
  --pink:#f0b8bb;
}
*{box-sizing:border-box;margin:0;padding:0}
html,body{width:1200px;height:3500px;overflow:hidden}
body{font-family:"Poppins",sans-serif;color:var(--ink);background:var(--white);position:relative}
.abs{position:absolute}
.serif{font-family:"Cinzel",serif}

/* header */
.site-header{top:0;left:0;width:1200px;height:160px;background:var(--white)}
.brand{left:120px;top:40px;display:flex;align-items:center;gap:12px}
.brand-mark{width:34px;height:34px;background:var(--red)}
.brand-name{font-family:"Cinzel",serif;font-weight:700;font-size:28px;color:var(--red);letter-spacing:1px}
.top-actions{top:30px;right:118px;display:flex;gap:14px}
.btn{display:inline-block;background:var(--red);color:var(--white);font-size:14px;font-weight:500;padding:8px 22px;border-radius:4px}
.main-nav{top:96px;right:118px;display:flex;gap:36px;font-size:15px;color:#333}
.main-nav span::after{content:" ▾";font-size:10px}

/* hero */
.hero{top:160px;left:0;width:1200px;height:720px}
.hero-copy{left:120px;top:110px;color:var(--white)}
.hero-copy .kicker{font-family:"Cinzel",serif;font-size:34px;font-weight:600;letter-spacing:1px}
.hero-copy h1{font-family:"Cinzel",serif;font-size:58px;font-weight:700;line-height:1.05;margin-top:4px}
.hero-copy .offer{font-size:21px;margin-top:18px;line-height:1.5}
.hero-buttons{margin-top:26px;display:flex;gap:14px}
.btn-white{background:var(--white);color:var(--red)}
.rates{margin-top:32px;display:flex;gap:38px}
.rate b{display:block;color:var(--rate);font-size:36px;font-weight:600;line-height:1}
.rate small{font-size:13px;color:#ddd}
.search{margin-top:26px;width:460px;height:46px;background:var(--white);border-radius:6px;display:flex;align-items:center;padding:0 16px;gap:12px;color:#888;font-size:14px}
.hero-photo{border-radius:26px}
.slider-arrows{top:612px;left:1020px;display:flex;gap:8px}
.slider-arrows span{width:48px;height:30px;border-radius:15px;background:#3a3a3a}
.slider-arrows span.on{background:var(--red)}

/* features */
.features{top:960px;left:0;width:1200px;display:flex;justify-content:space-between;padding:0 120px}
.feature{width:220px}
.feature svg{display:block;margin-bottom:16px}
.feature p{font-size:17px;font-weight:600;letter-spacing:.3px}

/* about */
.about-photo{left:110px;top:1240px;width:490px;height:410px}
.about-text{left:650px;top:1280px;width:440px}
.section-title{font-family:"Cinzel",serif;color:var(--red);font-weight:700}
.about-text h2{font-size:56px}
.about-text p{font-size:14px;color:var(--grey);line-height:1.85;margin-top:22px}
.btn-black{background:var(--black);color:var(--white);margin-top:34px}

/* listings */
.listings-head{top:1830px;left:120px;width:960px;display:flex;justify-content:space-between;align-items:center}
.listings-head h2{font-size:54px}
.listing{top:1935px;width:310px;height:395px;border-radius:22px;overflow:hidden}
.listing .tag{position:absolute;left:0;bottom:0;width:100%;height:80px;background:rgba(10,10,10,.85);color:var(--white);padding:14px 20px}
.tag .addr{font-size:13px}
.tag .price{font-size:22px;font-weight:700}
.tag .go{position:absolute;right:18px;top:22px;width:36px;height:36px;border-radius:50%;background:var(--white);display:flex;align-items:center;justify-content:center}

/* contact */
.contact{top:2340px;left:0;width:1200px;height:830px}
.contact h2{position:absolute;top:285px;width:1200px;text-align:center;font-size:54px;color:var(--red)}
.field{position:absolute;left:180px;width:400px;height:52px;background:var(--white);border-radius:5px;padding:14px 16px;font-size:14px;color:#777}
.message{position:absolute;left:620px;top:390px;width:395px;height:290px;background:var(--white);border-radius:5px;padding:14px 16px;font-size:14px;color:#777}
.send{position:absolute;left:180px;top:628px;width:400px;height:52px;background:var(--red);color:var(--white);border-radius:5px;text-align:center;font-size:17px;font-weight:600;line-height:52px}

/* footer */
.site-footer{top:3170px;left:0;width:1200px;height:330px;background:var(--red);color:var(--white)}
.footer-brand{left:70px;top:100px;display:flex;align-items:center;gap:14px}
.footer-brand .brand-mark{background:var(--white);width:44px;height:44px}
.footer-brand .brand-name{color:var(--white);font-size:38px}
.footer-col{top:60px}
.footer-col h4{font-family:"Cinzel",serif;font-size:21px;font-weight:700;margin-bottom:14px}
.footer-col li{list-style:none;font-size:14px;line-height:1.75}
.socials{display:flex;gap:10px;margin-top:12px}
.socials i{width:16px;height:16px;border-radius:50%;background:var(--white);display:block}
.copyright{left:0;top:302px;width:1200px;text-align:center;font-size:12px}
</style>
</head>
<body>

<header class="abs site-header">
  <div class="abs brand"><span class="brand-mark"></span><span class="brand-name">BRIGHTHOLD</span></div>
  <div class="abs top-actions">
    <span class="btn">Book An Appointment</span>
    <span class="btn">Contact Us Today ▾</span>
    <span class="btn">Login</span>
  </div>
  <nav class="abs main-nav">
    <span>Listings</span><span>Owners</span><span>Prospect Tenants</span><span>About</span><span>Community</span><span>Mortgage Info</span>
  </nav>
</header>

<section class="abs hero">
  <svg class="abs" style="top:0;left:0" width="1200" height="720" viewBox="0 0 1200 720">
    <polygon points="0,0 1200,0 1200,640 600,720 0,640" fill="#0c0c0c"/>
    <polyline points="0,640 600,712 1200,640" fill="none" stroke="#a6141b" stroke-width="6"/>
    <polyline points="0,655 600,730 1200,655" fill="none" stroke="#a6141b" stroke-width="2"/>
  </svg>
  <div class="abs hero-photo" style="left:660px;top:50px;width:360px;height:510px;background:linear-gradient(160deg,#e9e3d9,#c9bba6 55%,#8a7760)" role="img" aria-label="Family walking into their new home"></div>
  <div class="abs hero-photo" style="left:1035px;top:50px;width:200px;height:510px;background:linear-gradient(170deg,#e0dbd4,#b9b1a6 60%,#6a6158)" role="img" aria-label="Exterior of a rental home"></div>
  <div class="abs hero-copy">
    <div class="kicker">WELCOME TO</div>
    <h1>BRIGHTHOLD</h1>
    <p class="offer">Get 1 Month Property Management Fee Off.<br>$120 Value!</p>
    <div class="hero-buttons"><span class="btn">View Listings</span><span class="btn btn-white">Mortgage Info</span></div>
    <div class="rates">
      <div class="rate"><b>5.88%</b><small>30-Year Fixed Rate</small></div>
      <div class="rate"><b>7.19%</b><small>20-Year Fixed Rate</small></div>
      <div class="rate"><b>6.61%</b><small>15-Year Fixed Rate</small></div>
    </div>
    <div class="search">
      <svg width="16" height="16" viewBox="0 0 16 16"><circle cx="7" cy="7" r="5" fill="none" stroke="#888" stroke-width="2"/><line x1="11" y1="11" x2="15" y2="15" stroke="#888" stroke-width="2"/></svg>
      Enter Address, City, Zip, Neighborhood or MLS
    </div>
  </div>
  <div class="abs slider-arrows"><span></span><span class="on"></span></div>
</section>

<section class="abs features">
  <div class="feature">
    <svg width="70" height="70" viewBox="0 0 70 70"><polygon points="10,26 33,6 56,26 56,64 10,64" fill="#f0b8bb"/><polygon points="6,22 29,2 52,22 52,60 6,60" fill="#0c0c0c"/><rect x="20" y="30" width="18" height="16" fill="none" stroke="#fff" stroke-width="2"/></svg>
    <p>PROSPENT TENANTS</p>
  </div>
  <div class="feature">
    <svg width="70" height="70" viewBox="0 0 70 70"><polygon points="10,26 33,6 56,26 56,64 10,64" fill="#f0b8bb"/><polygon points="6,22 29,2 52,22 52,60 6,60" fill="#0c0c0c"/><rect x="21" y="27" width="16" height="22" fill="none" stroke="#fff" stroke-width="2"/><line x1="25" y1="34" x2="33" y2="34" stroke="#fff" stroke-width="2"/></svg>
    <p>TENANT APPLICATION</p>
  </div>
  <div class="feature">
    <svg width="70" height="70" viewBox="0 0 70 70"><polygon points="10,26 33,6 56,26 56,64 10,64" fill="#f0b8bb"/><polygon points="6,22 29,2 52,22 52,60 6,60" fill="#0c0c0c"/><circle cx="29" cy="34" r="6" fill="none" stroke="#fff" stroke-width="2"/><path d="M19 50 Q29 38 39 50" fill="none" stroke="#fff" stroke-width="2"/></svg>
    <p>RENTAL APPLICANTS</p>
  </div>
  <div class="feature">
    <svg width="70" height="70" viewBox="0 0 70 70"><polygon points="10,26 33,6 56,26 56,64 10,64" fill="#f0b8bb"/><polygon points="6,22 29,2 52,22 52,60 6,60" fill="#0c0c0c"/><rect x="20" y="26" width="18" height="24" fill="none" stroke="#fff" stroke-width="2"/><line x1="23" y1="32" x2="35" y2="32" stroke="#fff" stroke-width="2"/></svg>
    <p>MORTAGE CALCULATOR</p>
  </div>
</section>

<div class="abs about-photo" style="background:linear-gradient(135deg,#3a4658,#1e2633 60%,#5b2a30)" role="img" aria-label="Hand touching a property management interface"></div>
<section class="abs about-text">
  <h2 class="section-title">ABOUT US</h2>
  <p>Having the right property manager means having a partner who is committed to helping you and making being a home provider hassle free. We believe open communication, hard work, timely management, staying focused and knowledge go a long way in any business.</p>
  <p>This commitment has helped us build a remarkable track record of delivering results and maintaining a long lasting business partnership with our clients.</p>
  <span class="btn btn-black">Read More</span>
</section>

<div class="abs listings-head">
  <h2 class="section-title">OUR LISTINGS</h2>
  <span class="btn btn-black">View All Listings</span>
</div>
<article class="abs listing" style="left:120px;background:linear-gradient(180deg,#9fc3e8,#c9b99b 50%,#7e6a4c)" role="img" aria-label="Two-storey house with trees">
  <div class="tag"><div class="addr">812 Maple Row (Fairhaven)</div><div class="price">$2,000.00</div><span class="go"><svg width="14" height="14"><rect x="2" y="2" width="10" height="10" fill="#0c0c0c"/></svg></span></div>
</article>
<article class="abs listing" style="left:460px;background:linear-gradient(180deg,#3f7fd0,#8aa96a 50%,#5f5543)" role="img" aria-label="Single-storey house under blue sky">
  <div class="tag"><div class="addr">39 Orchard Ct #2 (Fairhaven)</div><div class="price">$2,000.00</div><span class="go"><svg width="14" height="14"><rect x="2" y="2" width="10" height="10" fill="#0c0c0c"/></svg></span></div>
</article>
<article class="abs listing" style="left:800px;background:linear-gradient(180deg,#f1efeb,#d8d2c8 55%,#9a8f80)" role="img" aria-label="Bright kitchen interior">
  <div class="tag"><div class="addr">514 Pine St. #6 (Fairhaven)</div><div class="price">$1,695.00</div><span class="go"><svg width="14" height="14"><rect x="2" y="2" width="10" height="10" fill="#0c0c0c"/></svg></span></div>
</article>

<section class="abs contact">
  <svg class="abs" style="top:0;left:0" width="1200" height="830" viewBox="0 0 1200 830">
    <defs><linearGradient id="contactBg" x1="0" y1="0" x2="0" y2="1"><stop offset="0" stop-color="#2a0c0e"/><stop offset="1" stop-color="#120607"/></linearGradient></defs>
    <polygon points="0,30 600,150 1200,30 1200,830 0,830" fill="url(#contactBg)" role="img" aria-label="Darkened house exterior background"/>
    <polyline points="0,10 600,130 1200,10" fill="none" stroke="#a6141b" stroke-width="16"/>
    <polyline points="0,40 600,160 1200,40" fill="none" stroke="#7d0d12" stroke-width="6"/>
  </svg>
  <h2>GET IN TOUCH WITH US</h2>
  <div class="field" style="top:390px">Full Name *</div>
  <div class="field" style="top:468px">Email Address *</div>
  <div class="field" style="top:546px">Contact Number *</div>
  <div class="send">Send Message</div>
  <div class="message">Message</div>
</section>

<footer class="abs site-footer">
  <div class="abs footer-brand"><span class="brand-mark"></span><span class="brand-name">BRIGHTHOLD</span></div>
  <div class="abs footer-col" style="left:460px">
    <h4>QUICK LINKS</h4>
    <ul><li>Listings</li><li>Owners</li><li>Prospect Tenants</li><li>Community</li><li>Mortgage Info</li></ul>
  </div>
  <div class="abs footer-col" style="left:670px">
    <h4>CONTACT US</h4>
    <ul><li>4410 Larkspur Way #12</li><li>Fairhaven, CA 90210</li><li>Phone (555) 204-7781</li><li>Mobile (555) 204-7790</li><li>BRE# 00000000</li></ul>
  </div>
  <div class="abs footer-col" style="left:910px">
    <h4>SUPPORT LINKS</h4>
    <ul><li>Support</li><li>Privacy Policy</li><li>Terms Of Use</li></ul>
    <div class="socials"><i></i><i></i><i></i><i></i><i></i><i></i></div>
  </div>
  <div class="abs copyright">(C) Copyright 2024 | All Rights Reserved.</div>
</footer>

</body>
</html>
```